Need Business Card for our Real Estate Business with Sales Executive's Picture

PANTONE 484 C ( RED)

PANTONE 2766 C ( BLUE

Industry/Entity Type

Real Estate

Contact Information for Business Card

Name, Mobile, email, & picture of Person
Agency Phone, address, Web address

Requirements
Must have
• Our Logo Colours, Agent Picture,

```html
<!DOCTYPE html>
<html lang="en">
<head>
<meta charset="utf-8">
<title>Mesa Realty Business Card</title>
<link rel="stylesheet" href="https://fonts.googleapis.com/css2?family=Open+Sans:ital,wght@0,400;0,600;0,700&display=swap">
<style>
  :root {
    --page: #3a3a3a;
    --card: #1c1c1d;
    --card-edge: #121213;
    --ink: #ffffff;
    --ink-soft: #d9d9d9;
    --ink-dim: #8a8a8a;
    --accent-red: #9b2a22;
    --suit-blue: #22357c;
    --photo-light: #4a4a4e;
  }
  * { margin: 0; padding: 0; box-sizing: border-box; }
  html, body { width: 799px; height: 1200px; overflow: hidden; }
  body {
    background: var(--page);
    font-family: "Open Sans", sans-serif;
    color: var(--ink);
    position: relative;
  }
  .card {
    position: absolute;
    left: 90px;
    width: 620px;
    height: 355px;
    background: var(--card);
    border-radius: 6px;
    box-shadow: 0 14px 30px rgba(0,0,0,.45);
    overflow: hidden;
  }
  .card-front { top: 120px; }
  .card-back { top: 710px; }

  /* front */
  .front-brand {
    position: absolute;
    left: 0; right: 0; top: 120px;
    text-align: center;
    font-size: 34px;
    font-weight: 600;
    letter-spacing: 6px;
    color: #3b3b3d;
  }
  .front-web {
    position: absolute;
    left: 0; right: 0; bottom: 62px;
    display: flex;
    align-items: center;
    justify-content: center;
    gap: 22px;
    font-size: 15px;
    color: var(--ink-soft);
    letter-spacing: .5px;
  }
  .front-web .rule { width: 60px; height: 2px; background: var(--accent-red); }

  /* back */
  .brand {
    position: absolute;
    left: 40px; top: 36px;
    display: flex; align-items: center; gap: 10px;
    font-size: 34px; font-weight: 600; letter-spacing: 4px;
    color: var(--ink);
  }
  .brand .mark { width: 10px; height: 10px; background: var(--accent-red); }
  .agent { position: absolute; left: 40px; top: 118px; }
  .agent-name { font-size: 22px; font-weight: 700; line-height: 1.2; }
  .agent-title { font-size: 14px; color: var(--ink-soft); margin-bottom: 12px; }
  .contact-list { list-style: none; }
  .contact-list li {
    display: flex; align-items: flex-start; gap: 10px;
    font-size: 14px; line-height: 20px; color: var(--ink);
  }
  .contact-list svg { width: 12px; height: 12px; margin-top: 4px; flex: none; fill: var(--accent-red); }
  .photo {
    position: absolute;
    right: 0; bottom: 0;
    width: 250px; height: 300px;
    background: linear-gradient(180deg, var(--photo-light) 0%, #3a3c4a 45%, var(--suit-blue) 75%, #1a2a66 100%);
    clip-path: polygon(28% 0, 80% 0, 100% 62%, 100% 100%, 0 100%, 0 78%, 22% 60%);
  }
</style>
</head>
<body>
  <section class="card card-front">
    <div class="front-brand">MESA REALTY</div>
    <div class="front-web"><span class="rule"></span><span>www.mesarealty.com</span><span class="rule"></span></div>
  </section>

  <section class="card card-back">
    <div class="brand"><span class="mark"></span>MESA REALTY</div>
    <div class="agent">
      <div class="agent-name">Dana Whitfield</div>
      <div class="agent-title">Managing Director</div>
      <ul class="contact-list">
        <li><svg viewBox="0 0 12 12"><rect x="3" y="0" width="6" height="12" rx="1.5"/></svg>555.210.4478</li>
        <li><svg viewBox="0 0 12 12"><path d="M1 4h10v7H1z M2 1h8l1 3H1z"/></svg>555-318-6620</li>
        <li><svg viewBox="0 0 12 12"><path d="M0 2h12v8H0z" /></svg>dwhitfield@mesarealty.com</li>
        <li><svg viewBox="0 0 12 12"><circle cx="6" cy="6" r="6"/></svg>www.mesarealty.com</li>
        <li><svg viewBox="0 0 12 12"><path d="M6 0a4 4 0 0 1 4 4c0 3-4 8-4 8S2 7 2 4a4 4 0 0 1 4-4z"/></svg>48 Harbor Lane #210,<br>Fairview, CO 80011</li>
      </ul>
    </div>
    <div class="photo" role="img" aria-label="Portrait photo of the sales executive in a blue suit"></div>
  </section>
</body>
</html>
```